The most modern business card ever !!!

Our company call “Vendalo”. Vendalo is a technology company specialized in cruises solutions. Out main product is a platform to reserve cruises. This is a revolutionary platform that make easier to travel agencies and final users to reserve cruises across dozen companies like tibba, wernu, hpv, dgb, etc..We are a “start up”, with a young team of developers and we want to transmit it.. For it, we want something different, a modern business card that represent cruises and technology.. When someone receive this card, this person should say: wowww this is different… this is modern… this is a cruise related company..
- diferent, modern
- traditions business card

```html
<!DOCTYPE html>
<html lang="en">
<head>
<meta charset="utf-8">
<title>Vendalo Business Card</title>
<link rel="stylesheet" href="https://fonts.googleapis.com/css2?family=Roboto:wght@400;500;700&display=swap">
<style>
  :root {
    --teal-dark: #36656a;
    --teal-mid: #2a8a87;
    --teal-strip: #267777;
    --icon-blue: #2ea8df;
    --ink: #1c1c1c;
    --paper: #ffffff;
    --mist: #e6f3f3;
  }
  * { margin: 0; padding: 0; box-sizing: border-box; }
  html, body { width: 1200px; height: 1200px; overflow: hidden; background: var(--paper); }
  body { position: relative; font-family: "Roboto", sans-serif; color: var(--ink); }

  .card { position: absolute; overflow: hidden; }

  .card-front {
    left: 328px; top: 314px; width: 402px; height: 245px;
    background: radial-gradient(ellipse at 50% 52%, var(--teal-mid) 0%, #2b7f7e 40%, var(--teal-dark) 85%);
    border: 1px solid #27494d;
  }
  .front-brand {
    position: absolute; left: 0; right: 0; top: 102px;
    text-align: center; font-size: 32px; font-weight: 500; letter-spacing: 1px; color: var(--ink);
  }
  .front-web {
    position: absolute; left: 0; right: 0; top: 138px;
    text-align: center; font-size: 11px; letter-spacing: 4.5px; color: #e8f4f4;
  }

  .card-back {
    left: 478px; top: 646px; width: 393px; height: 240px;
    background: var(--paper); border: 1px solid #555;
  }
  .back-strip { position: absolute; left: 0; top: 0; width: 42px; height: 100%; background: var(--teal-strip); }
  .back-pattern {
    position: absolute; left: 76px; top: 22px; width: 300px; height: 210px; border-radius: 20px;
    background: radial-gradient(ellipse at 40% 50%, var(--mist) 0%, rgba(230,243,243,0.4) 60%, rgba(255,255,255,0) 100%);
  }
  .contact { position: absolute; left: 27px; display: flex; align-items: center; gap: 14px; }
  .contact-icon {
    width: 30px; height: 30px; border-radius: 50%; background: var(--icon-blue);
    display: flex; align-items: center; justify-content: center;
  }
  .contact-label { font-size: 13.5px; font-weight: 500; line-height: 1.1; }
  .contact-value { font-size: 8px; font-weight: 500; margin-top: 2px; }
  .contact-phone { top: 70px; }
  .contact-mail { top: 121px; }
  .contact-address { top: 172px; gap: 10px; }

  .person-icon {
    position: absolute; left: 273px; top: 105px; width: 30px; height: 30px; border-radius: 50%;
    background: var(--icon-blue); display: flex; align-items: center; justify-content: center;
  }
  .identity {
    position: absolute; left: 318px; top: 120px; transform-origin: 0 0; transform: rotate(-90deg) translate(-50%, -50%);
    text-align: center; white-space: nowrap;
  }
  .identity-name { font-size: 13px; letter-spacing: 0.5px; }
  .identity-name b { font-weight: 700; }
  .identity-role { font-size: 6px; letter-spacing: 0.3px; }
  .back-brand {
    position: absolute; left: 372px; top: 120px; transform: translate(-50%, -50%) rotate(-90deg);
    font-size: 24px; font-weight: 500; white-space: nowrap; color: var(--ink);
  }
  .back-accent { position: absolute; right: 0; top: 76px; width: 7px; height: 92px; background: var(--teal-strip); }
</style>
</head>
<body>
  <section class="card card-front">
    <div class="front-brand">Vendalo</div>
    <div class="front-web">www.vendalo.com</div>
  </section>

  <section class="card card-back">
    <div class="back-strip"></div>
    <div class="back-pattern" role="img" aria-label="Soft background of faint overlapping rounded tiles"></div>

    <div class="contact contact-phone">
      <span class="contact-icon"><svg width="12" height="12" viewBox="0 0 24 24"><path fill="#1c1c1c" d="M6.6 10.8a15 15 0 0 0 6.6 6.6l2.2-2.2a1 1 0 0 1 1-.25 11.4 11.4 0 0 0 3.6.57 1 1 0 0 1 1 1V20a1 1 0 0 1-1 1A17 17 0 0 1 3 4a1 1 0 0 1 1-1h3.5a1 1 0 0 1 1 1c0 1.25.2 2.45.57 3.57a1 1 0 0 1-.25 1z"/></svg></span>
      <div><div class="contact-label">Your Phone</div><div class="contact-value">+610-555-0142</div></div>
    </div>
    <div class="contact contact-mail">
      <span class="contact-icon"><svg width="13" height="10" viewBox="0 0 26 20"><rect x="1" y="1" width="24" height="18" rx="2" fill="#1c1c1c"/><path d="M3 4l10 7 10-7" stroke="#2ea8df" stroke-width="2" fill="none"/></svg></span>
      <div><div class="contact-label">Your E-mail</div><div class="contact-value">hello@vendalo.com</div></div>
    </div>
    <div class="contact contact-address">
      <span class="contact-icon"><svg width="10" height="13" viewBox="0 0 20 26"><rect x="2" y="1" width="16" height="24" rx="1" fill="#1c1c1c"/><rect x="6" y="4" width="8" height="8" fill="#2ea8df"/></svg></span>
      <div><div class="contact-label">Your Adress</div><div class="contact-value" style="font-weight:400">Porto Vale, Marenia</div></div>
    </div>

    <span class="person-icon"><svg width="14" height="14" viewBox="0 0 24 24"><circle cx="14" cy="12" r="7" fill="#1c1c1c"/><ellipse cx="6" cy="12" rx="4" ry="6" fill="#1c1c1c"/></svg></span>
    <div class="identity">
      <div class="identity-name"><b>YOUR</b> NAME</div>
      <div class="identity-role">YOUR POSITION</div>
    </div>
    <div class="back-brand">Vendalo</div>
    <div class="back-accent"></div>
  </section>
</body>
</html>
```